Brintel Works - Fast, Efficient and Gas Mainteance for Domestic, Commercial and Industrial clients

We are in the process of purchasing a new business and would like to get a new logo and business card.
Business is a gas maintenance business that also does new gas installations.
Has been established since 1988.
Services include:
Install all types of gas appliances & equipment inc. hot water units
Maintain / repair / replace all types of gas appliances & equipment

Target Market(s)

Domestic, Commercial and Industrial clients

Industry/Entity Type

Business

Contact Information for Business Card

admin@brintelworks.com.au
07 3918 4726
Brintel Works PTY LTD

Logo Text

Gas Fitting & Plumbing Maintenance Specialists

Font styles to use
Sans Serif

Requirements
Must have
• Logo
• Business name, contact number, email address, web address
• Domestic | Commercial | Industrial Est Since 1988
Nice to have
• Possibly a black card with a flame logo to one side
Should not have
• Spelling errors

```html
<!DOCTYPE html>
<html lang="en">
<head>
<meta charset="utf-8">
<title>Brintel Works PTY LTD – Business Card</title>
<link href="https://fonts.googleapis.com/css2?family=Open+Sans:wght@400;600;700&display=swap" rel="stylesheet">
<style>
  :root {
    --backdrop: #3b3431;
    --card: #161616;
    --card-edge: #232323;
    --flame-orange: #f6a01a;
    --flame-yellow: #fcd116;
    --text-light: #f2f2f2;
  }
  * { margin: 0; padding: 0; box-sizing: border-box; }
  html, body {
    width: 1200px; height: 844px; overflow: hidden;
    background: var(--backdrop);
    font-family: "Open Sans", Arial, sans-serif;
  }
  .stage { position: relative; width: 1200px; height: 844px; }

  .card {
    position: absolute;
    width: 520px; height: 300px;
    background: var(--card);
    border: 1px solid var(--card-edge);
    border-radius: 4px;
    box-shadow: 0 10px 24px rgba(0,0,0,.45);
    top: 272px;
  }
  .card--contact { left: 50px; }
  .card--front { left: 630px; }

  .brand { color: var(--flame-yellow); font-weight: 700; text-align: center; line-height: 1; }
  .brand__mark {
    display: block; width: 34px; height: 34px; margin: 0 auto 12px;
    border-radius: 50%; background: var(--flame-orange);
  }
  .brand__name { font-size: 34px; letter-spacing: .5px; }
  .brand__suffix { display: block; font-size: 12px; letter-spacing: 4px; margin-top: 6px; }

  .card--contact .brand { position: absolute; left: 40px; top: 62px; width: 270px; }
  .card--contact .brand__name { font-size: 30px; }

  .contact-list {
    position: absolute; right: 26px; top: 120px;
    list-style: none; text-align: right;
    color: var(--text-light); font-size: 14px; line-height: 24px;
  }
  .contact-list li { display: flex; justify-content: flex-end; align-items: center; gap: 8px; }
  .contact-list svg { width: 12px; height: 12px; fill: none; stroke: var(--flame-orange); stroke-width: 2; }
  .contact-list .icon-gap { width: 12px; display: inline-block; }

  .address {
    position: absolute; left: 30px; bottom: 30px;
    color: var(--text-light); font-size: 16px; line-height: 24px;
  }

  .card--front .brand { position: absolute; left: 0; right: 0; top: 70px; }
  .tagline {
    position: absolute; left: 0; right: 0; top: 212px; text-align: center;
    color: var(--flame-orange); font-size: 14px;
  }
</style>
</head>
<body>
<main class="stage">
  <section class="card card--contact" aria-label="Business card, contact side">
    <div class="brand">
      <span class="brand__mark"></span>
      <span class="brand__name">Brintel Works</span>
      <span class="brand__suffix">PTY LTD</span>
    </div>
    <ul class="contact-list">
      <li>07 3918 4726
        <svg viewBox="0 0 12 12" aria-hidden="true"><path d="M2 1.5 L4 1.5 L5 4 L3.8 5 Q5 7.5 7 8.2 L8 7 L10.5 8 L10.5 10 Q6 11 2.5 6.5 Q1 4 2 1.5Z"/></svg></li>
      <li>admin@brintelworks.com.au
        <svg viewBox="0 0 12 12" aria-hidden="true"><rect x="1" y="2.5" width="10" height="7"/><path d="M1 2.5 L6 6.5 L11 2.5"/></svg></li>
      <li>www.brintelworks.com.au
        <svg viewBox="0 0 12 12" aria-hidden="true"><circle cx="6" cy="6" r="4.5"/><path d="M1.5 6 H10.5 M6 1.5 Q3.5 6 6 10.5 M6 1.5 Q8.5 6 6 10.5"/></svg></li>
    </ul>
    <address class="address" style="font-style:normal">
      12345, Address Goes Here<br>Country Name, 123456
    </address>
  </section>

  <section class="card card--front" aria-label="Business card, front side">
    <div class="brand">
      <span class="brand__mark"></span>
      <span class="brand__name">Brintel Works</span>
      <span class="brand__suffix">PTY LTD</span>
    </div>
    <p class="tagline">Domestic | Commercial | Industrial Est Since 1988</p>
  </section>
</main>
</body>
</html>
```